Stationary design for boutique production house

We need a stationary design for our production house, 'Lorno Productions' based in Singapore. We produce microfilms as well as podcasts, talkshows and events. Our logo is a stylized icon of our director, who is also the executive producer and host of our programs, Lorno. Our main company colors are Red, Black and white. We would like a clean, minimalist design incorporating our existing company logo that conveys a sense of urbanism and elegance.

Logo and font files are attached. f

Target Market(s)

We focus on lifestyle media rather than entertainment.

Industry/Entity Type

Boutique

Font styles to use
Serif
Sans Serif

Colors
ec1f27
ffffff
000000

Requirements
Must have
• Our company logo and at least one of our company colors.
Nice to have
• Our address and contact information.
Should not have
• Changes made to the company logo (using only certain parts of it is fine though)

```html
<!DOCTYPE html>
<html lang="en">
<head>
<meta charset="utf-8">
<title>Lorno Productions Stationery</title>
<link rel="stylesheet" href="https://fonts.googleapis.com/css2?family=Roboto:wght@400;500;700&display=swap">
<style>
  :root {
    --red: #ec1f27;
    --charcoal: #333333;
    --white: #ffffff;
    --paper-edge: #e2e2e2;
    --ground: #efefef;
    --ink: #444444;
  }
  * { margin: 0; padding: 0; box-sizing: border-box; }
  html, body { width: 1200px; height: 937px; overflow: hidden; background: var(--ground); }
  .canvas { position: relative; width: 1200px; height: 937px; font-family: "Roboto", Arial, sans-serif; color: var(--ink); }
  address { font-style: normal; }
  .sheet { position: absolute; background: var(--white); border: 1px solid var(--paper-edge); overflow: hidden; }
  .sheet .swoosh { position: absolute; inset: 0; width: 100%; height: 100%; }
  .brand { position: absolute; display: flex; align-items: center; justify-content: center; }
  .brand-name { font-family: "Roboto", Arial, sans-serif; font-weight: 500; color: var(--charcoal); line-height: 1; letter-spacing: 0.04em; }

  /* letterhead */
  .letterhead { left: 185px; top: 68px; width: 387px; height: 544px; }
  .letterhead .brand { left: 18px; top: 22px; width: 120px; height: 150px; }
  .letterhead .brand-name { font-size: 30px; }
  .letter-contact { position: absolute; left: 303px; top: 22px; font-size: 4.6px; line-height: 7px; color: var(--ink); }
  .letter-contact strong { font-weight: 700; }
  .letter-body { position: absolute; left: 36px; top: 202px; width: 290px; font-size: 5.4px; line-height: 7.6px; }
  .letter-body p { margin-bottom: 8px; }
  .letter-body .spaced { margin-bottom: 22px; }
  .signature { width: 40px; height: 18px; background: #d9d9d9; margin: 4px 0 6px; }

  /* cover */
  .cover { left: 636px; top: 40px; width: 458px; height: 576px; }
  .cover .brand { left: 100px; top: 160px; width: 260px; height: 290px; }
  .cover .brand-name { font-size: 56px; }
  .web { position: absolute; color: var(--white); font-size: 13px; letter-spacing: 0.2em; }
  .cover .web { right: 16px; bottom: 12px; }

  /* cards */
  .card { width: 176px; height: 100px; border-radius: 6px; }
  .card-front { left: 46px; top: 658px; }
  .card-back { left: 46px; top: 785px; }
  .card-front .brand { left: 4px; top: 8px; width: 56px; height: 44px; }
  .card-front .brand-name { font-size: 12px; }
  .card-contact { position: absolute; left: 6px; top: 56px; font-size: 3.6px; line-height: 5.2px; }
  .card-holder { position: absolute; left: 100px; top: 60px; font-size: 4.4px; line-height: 6px; }
  .card-holder strong { font-weight: 500; letter-spacing: 0.04em; }
  .card-back .brand { left: 48px; top: 22px; width: 80px; height: 56px; }
  .card-back .brand-name { font-size: 15px; }

  /* envelopes */
  .envelope { width: 431px; height: 208px; }
  .envelope-front { left: 265px; top: 672px; }
  .envelope-front .brand { left: 10px; top: 18px; width: 110px; height: 120px; }
  .envelope-front .brand-name { font-size: 24px; }
  .envelope-back { left: 737px; top: 671px; }
  .flap { position: absolute; left: 0; top: 0; width: 100%; height: 72px; background: var(--charcoal); border-radius: 0 0 40px 40px; }
  .envelope-back .web { left: 0; right: 0; top: 26px; text-align: center; }
</style>
</head>
<body>
<main class="canvas">

  <section class="sheet letterhead" aria-label="Letterhead">
    <svg class="swoosh" viewBox="0 0 387 544" preserveAspectRatio="none" aria-hidden="true">
      <path d="M387 440 C378 480 362 515 340 544 L387 544 Z" fill="var(--red)"/>
      <path d="M387 370 C378 450 330 515 205 544 L330 544 C365 505 385 450 387 405 Z" fill="var(--charcoal)"/>
    </svg>
    <div class="brand"><span class="brand-name">Lorno</span></div>
    <address class="letter-contact">
      <strong>12 Kallang Quay, Level 3</strong><br>
      <strong>Singapore 338721</strong><br>
      +65 6123 4567<br>
      hello@lornoproductions.sg<br>
      www.lornoproductions.sg
    </address>
    <div class="letter-body">
      <p>July 2, 2024</p>
      <p><strong>Dear Client,</strong><br>12 Kallang Quay, Singapore</p>
      <p>Thank you for choosing our studio for your next production. We craft microfilms, podcasts, talkshows and live events with a calm, careful eye for lifestyle stories. Our small team works closely with every partner, from the first idea to the final cut, so each piece feels personal and finished.</p>
      <p class="spaced">We look forward to planning the schedule with you and will share a first outline of the shoot within the week.</p>
      <p>Please find the proposal attached. It covers the format, crew, locations and budget, with room for your notes. Should anything need a change, simply reply to this letter or call our office and we will adjust the plan together before filming begins.</p>
      <p>Best Regards,</p>
      <div class="signature" role="img" aria-label="Handwritten signature"></div>
      <p><strong>Daniel Tan</strong><br>Director<br><br>12 Kallang Quay, Singapore</p>
    </div>
  </section>

  <section class="sheet cover" aria-label="Presentation folder">
    <svg class="swoosh" viewBox="0 0 458 576" preserveAspectRatio="none" aria-hidden="true">
      <path d="M290 0 L458 0 L458 185 C430 110 370 40 290 0 Z" fill="var(--red)"/>
      <path d="M325 48 C420 110 458 200 458 260 L458 576 L150 576 C420 430 470 200 325 48 Z" fill="var(--charcoal)"/>
    </svg>
    <div class="brand"><span class="brand-name">Lorno</span></div>
    <p class="web">www.lornoproductions.sg</p>
  </section>

  <section class="sheet card card-front" aria-label="Business card front">
    <svg class="swoosh" viewBox="0 0 176 100" preserveAspectRatio="none" aria-hidden="true">
      <path d="M135 0 L176 0 L176 40 C168 20 155 6 135 0 Z" fill="var(--red)"/>
      <path d="M150 6 C170 20 176 38 176 48 L176 100 L140 100 C175 75 178 35 150 6 Z" fill="var(--charcoal)"/>
    </svg>
    <div class="brand"><span class="brand-name">Lorno</span></div>
    <address class="card-contact">12 Kallang Quay, Level 3<br>Singapore 338721<br><br>+65 6123 4567<br>hello@lornoproductions.sg<br>www.lornoproductions.sg</address>
    <p class="card-holder"><strong>RACHEL LIM</strong><br>Managing Director</p>
  </section>

  <section class="sheet card card-back" aria-label="Business card back">
    <div class="brand"><span class="brand-name">Lorno</span></div>
  </section>

  <section class="sheet envelope envelope-front" aria-label="Envelope front">
    <svg class="swoosh" viewBox="0 0 431 208" preserveAspectRatio="none" aria-hidden="true">
      <path d="M330 0 L431 0 L431 75 C405 35 370 10 330 0 Z" fill="var(--red)"/>
      <path d="M355 8 C415 40 431 80 431 95 L431 208 L250 208 C420 150 440 60 355 8 Z" fill="var(--charcoal)"/>
    </svg>
    <div class="brand"><span class="brand-name">Lorno</span></div>
  </section>

  <section class="sheet envelope envelope-back" aria-label="Envelope back">
    <div class="flap"></div>
    <p class="web">www.lornoproductions.sg</p>
  </section>

</main>
</body>
</html>
```